Website design for legal tech start up in Switzerland (B2B)

We are for a legal tech start up in Switzerland called KOVA. We have been running since August 2016. This will be our first live website.

We need a website designed and business card design for our start-up in Switzerland. We also need the Web design to be converted into HTML and CSS files.

Function of website:
• To inform potential customers of our services
• Form a key part of our digital marketing and sales footprint.
• Branding

Please find attached logo.
Updates

Project Deadline Extended Reason: Giving us time to review submissions and provide opportunity for more submissions. Added Thursday, February 16, 2017

Project Deadline Extended
Reason: Looking for more idea's not necessarily set on blue and grey colours only.

Target Market(s)

B2B tech powered legal services.

Industry/Entity Type

Legal

Contact Information for Business Card

Lean and slick design.

Coding

Coded - Design and coding required

Number of Pages Required

5+ page

Requirements
Must have
• VERY LEAN AND CLEAN DESIGN!
• We have received many great standard designs, but we are looking for something more out-of-the box: You can get inspiration from these designs: http://www.pixelvane.com/websites/clean/
• Thanks!!
• Easy content management system
• Well structured coding for additional development
• Responsive webpage for all types of devices
• SEO optimized
• Tabs (Home, services, team, careers, blog, contact us)
• Colour scheme complementary to logo
Nice to have
• Look and Design - Approachable, High-tech, Modern
• Easy to add chat bot capability in future
Should not have
• Too busy/ too much clutter
• Not take to long to load

```html
<!DOCTYPE html>
<html lang="en">
<head>
<meta charset="utf-8">
<title>KOVA – Legal Services</title>
<link rel="stylesheet" href="https://fonts.googleapis.com/css2?family=Roboto:ital,wght@0,400;0,500;0,700;1,400&display=swap">
<style>
:root{
  --navy:#2a4a8a;
  --navy-deep:#1f3c78;
  --blue:#4a74b8;
  --blue-light:#5d8ad0;
  --grey-panel:#5e5e5e;
  --bg-soft:#f3f4f6;
  --card-bg:#f0f1f3;
  --ink:#1d1d1d;
  --muted:#6a6a6a;
  --white:#ffffff;
  --line:#d6d8dc;
}
*{box-sizing:border-box;margin:0;padding:0}
html,body{width:1200px;height:2317px;overflow:hidden}
body{font-family:'Roboto',Arial,sans-serif;color:var(--ink);background:var(--white);position:relative}
.abs{position:absolute}

/* Hero */
.hero{position:absolute;left:0;top:0;width:1200px;height:544px;
  background:linear-gradient(115deg,#3b3f46 0%,#5a5f66 30%,#2e3238 55%,#6b6f74 80%,#45484d 100%)}
.hero::after{content:"";position:absolute;inset:0;background:rgba(20,24,32,.35)}
.header{position:absolute;left:0;top:0;width:1200px;height:66px;border-bottom:1px solid rgba(255,255,255,.2);z-index:2}
.brand{position:absolute;left:54px;top:12px;font-size:38px;font-weight:500;letter-spacing:3px;color:var(--white)}
.nav{position:absolute;left:345px;top:22px;display:flex;gap:35px}
.nav a{color:var(--white);text-decoration:none;font-size:15px;font-weight:500}
.hdr-btn{position:absolute;top:15px;height:33px;border-radius:17px;font-size:14px;font-weight:500;display:flex;align-items:center;justify-content:center}
.btn-chat{left:970px;width:65px;border:2px solid var(--white);color:var(--white)}
.btn-eval{left:1038px;width:116px;background:var(--white);color:var(--ink)}
.hero-copy{position:absolute;left:350px;top:230px;width:500px;text-align:center;color:var(--white);z-index:2}
.hero-copy h1{font-size:19px;font-weight:700;margin-bottom:12px}
.hero-copy p{font-size:10.5px;line-height:23px;opacity:.9}
.btn-outline{display:inline-block;border:1.5px solid var(--white);color:var(--white);font-size:12px;font-weight:500;padding:10px 16px;border-radius:3px;margin-top:14px}

/* Welcome band */
.welcome{position:absolute;left:0;top:544px;width:1200px;height:110px;
  background:linear-gradient(90deg,#284a8a 0%,#3a64a8 55%,#5c8bd2 100%);color:var(--white);text-align:center}
.welcome h2{font-size:21px;font-weight:700;margin-top:7px}
.welcome .rule{position:absolute;left:51px;width:1098px;top:42px;border-top:1.5px dashed rgba(255,255,255,.8)}
.welcome p{position:absolute;left:60px;width:1080px;top:60px;font-size:12.5px;line-height:18px}

/* Services tabs */
.services{position:absolute;left:0;top:654px;width:1200px;height:308px;background:var(--bg-soft)}
.tab{position:absolute;top:21px;height:46px;font-size:15px;font-weight:500;display:flex;align-items:center;justify-content:center}
.tab.active{border:1.5px solid var(--navy);border-radius:3px;color:var(--navy);background:var(--white)}
.services .rule{position:absolute;left:37px;width:1126px;top:81px;border-top:1.5px dashed var(--blue)}
.svc-card{position:absolute;top:125px;width:253px;height:125px;border-radius:3px}
.svc-icon{position:absolute;top:101px;width:46px;height:46px;border-radius:50%;background:var(--navy);display:flex;align-items:center;justify-content:center}
.svc-label{position:absolute;top:230px;width:233px;height:43px;background:linear-gradient(90deg,#2d5095,#5a88cc);color:var(--white);font-size:17px;font-weight:500;display:flex;align-items:center;justify-content:center;border-radius:2px}

/* Contact & in-house */
.mail{position:absolute;left:0;top:962px;width:600px;height:197px;background:var(--navy);color:var(--white)}
.mail h2{position:absolute;left:0;width:600px;top:20px;text-align:center;font-size:27px;font-weight:500}
.field{position:absolute;width:241px;height:32px;background:var(--white);border-radius:3px;font-size:12px;color:#999;padding:9px 12px}
.send{position:absolute;width:241px;height:32px;background:var(--white);border-radius:3px;font-size:12px;color:var(--ink);font-weight:500;text-align:center;padding-top:9px}
.inhouse{position:absolute;left:600px;top:962px;width:600px;height:197px;background:var(--grey-panel);color:var(--white);text-align:center}
.inhouse h2{margin-top:20px;font-size:27px;font-weight:500}
.inhouse p{width:520px;margin:12px auto 0;font-size:14.5px;line-height:22px}
.inhouse .btn-outline{margin-top:8px;padding:8px 15px}

/* Blog */
.section-title{position:absolute;left:0;width:1200px;text-align:center;font-size:21px;font-weight:500}
.section-title span{color:var(--navy)}
.section-rule{position:absolute;left:51px;width:1098px;border-top:1.5px dashed var(--blue)}
.post{position:absolute;top:1240px;width:253px;height:356px;background:var(--card-bg)}
.post-img{height:189px}
.post h3{font-size:17px;font-weight:500;margin:14px 19px 6px}
.post p{font-size:12.5px;line-height:20px;color:var(--muted);margin:0 19px}
.post-meta{position:absolute;left:19px;right:19px;top:308px;border-top:1px solid var(--line);padding-top:17px;font-size:11px;color:var(--muted);display:flex;justify-content:space-between;align-items:center}
.post-meta span{display:flex;align-items:center;gap:6px}

/* Testimonials */
.testimonials{position:absolute;left:0;top:1619px;width:1200px;height:212px;background:var(--bg-soft)}
.quote{position:absolute;top:103px;width:411px;font-size:12.5px;font-style:italic;color:var(--muted);line-height:20px}
.quote cite{display:block;font-style:normal;color:var(--ink);margin-top:8px;font-size:13px}
.avatar{position:absolute;top:104px;width:77px;height:77px;border-radius:50%;background:radial-gradient(circle,#c9b8a6,#8f7c6c)}
.divider-v{position:absolute;left:600px;top:105px;height:73px;border-left:1.5px dashed var(--blue)}

/* Like bar */
.likebar{position:absolute;left:0;top:1831px;width:1200px;height:72px;background:var(--white)}
.likebar .line{position:absolute;left:66px;width:1068px;top:35px;border-top:1px solid var(--line)}
.like-pill{position:absolute;left:377px;top:12px;width:448px;height:46px;border:1px solid var(--line);border-radius:23px;background:var(--white);display:flex;align-items:center}
.like-pill .thumb{width:58px;height:100%;border-right:1px solid var(--line);display:flex;align-items:center;justify-content:center}
.like-btn{margin-left:38px;background:#4267b2;color:var(--white);font-size:10px;font-weight:700;padding:3px 7px;border-radius:2px}
.like-pill small{font-size:10px;margin-left:6px;color:#333}

/* Footer */
.footer{position:absolute;left:0;top:1903px;width:1200px;height:414px;
  background:linear-gradient(110deg,#23437f 0%,#2f5396 50%,#4b78bf 100%);color:var(--white)}
.footer h4{position:absolute;top:28px;font-size:17px;font-weight:500}
.footer p{font-size:12.5px;line-height:19px}
.contact-col{position:absolute;left:51px;top:71px;width:255px}
.contact-col p{margin-bottom:15px}
.contact-col b{font-weight:500}
.socials{display:flex;gap:13px;margin-top:2px}
.socials i{width:11px;height:11px;border-radius:50%;background:var(--white);display:block}
.map{position:absolute;left:334px;top:70px;width:534px;height:225px;background:linear-gradient(135deg,#e8e2d3 0%,#cfe0c4 35%,#a9cbe6 55%,#ece6d8 80%)}
.about-col{position:absolute;left:896px;top:71px;width:255px}
.about-col p{margin-bottom:13px}
.footer .rule{position:absolute;left:51px;width:1098px;top:349px;border-top:1px solid rgba(255,255,255,.5)}
.copy{position:absolute;top:378px;font-size:12px;font-weight:500}
.foot-brand{position:absolute;left:0;width:1200px;top:362px;text-align:center;font-size:34px;font-weight:500;letter-spacing:3px}
</style>
</head>
<body>

<section class="hero" role="img" aria-label="Photo of lawyers in a business discussion"></section>
<header class="header">
  <div class="brand">KOVA</div>
  <nav class="nav">
    <a href="#">HOME</a><a href="#">SERVICES</a><a href="#">TEAM</a><a href="#">CAREERS</a><a href="#">BLOG</a><a href="#">CONTACT</a>
  </nav>
  <div class="hdr-btn btn-chat">Chat</div>
  <div class="hdr-btn btn-eval">Free Evaluation</div>
</header>
<div class="hero-copy">
  <h1>We Provide Legal Help for Felonies</h1>
  <p>At vero eos et accusamus et iusto odio dignissimos ducimus qui blanditiis praesentium<br>voluptatum deleniti atque corrupti quos dolores et quas molestias excepturi sint<br>occaecati cupiditate non provident.</p>
  <span class="btn-outline">LEARN MORE</span>
</div>

<section class="welcome">
  <h2>Welcome to Kova</h2>
  <div class="rule"></div>
  <p>Sed ut perspiciatis unde omnis iste natus error sit voluptatem accusantium doloremque laudantium, totam rem aperiam, eaque ipsa quae ab illo inventore veritatis et quasi architecto beatae vitae dicta sunt explicabo</p>
</section>

<section class="services">
  <div class="tab active" style="left:281px;width:161px">Criminal Charges</div>
  <div class="tab" style="left:468px;width:126px">Estate Planning</div>
  <div class="tab" style="left:632px;width:115px">In House legal</div>
  <div class="tab" style="left:788px;width:122px">Personal Injury</div>
  <div class="rule"></div>

  <div class="svc-card" style="left:52px;background:linear-gradient(135deg,#8a6a55,#c9a58a)" role="img" aria-label="Photo of hands in handcuffs"></div>
  <div class="svc-card" style="left:333px;background:linear-gradient(135deg,#e6ddc8,#b89c72)" role="img" aria-label="Photo of a model house on documents"></div>
  <div class="svc-card" style="left:614px;background:linear-gradient(135deg,#6d8fb8,#b9c9da)" role="img" aria-label="Photo of city office towers"></div>
  <div class="svc-card" style="left:894px;background:linear-gradient(135deg,#6e4a3c,#2c4e86)" role="img" aria-label="Photo of a distressed driver after a car accident"></div>

  <div class="svc-icon" style="left:155px"><svg width="22" height="22" viewBox="0 0 22 22"><rect x="4" y="4" width="10" height="5" fill="#fff" transform="rotate(-35 9 6)"/><rect x="9" y="9" width="3" height="11" fill="#fff" transform="rotate(-35 10 14)"/><rect x="2" y="18" width="10" height="2" fill="#fff"/></svg></div>
  <div class="svc-icon" style="left:436px"><svg width="22" height="22" viewBox="0 0 22 22"><path d="M3 11 11 4 19 11V19H3Z" fill="#fff"/><rect x="9" y="13" width="4" height="6" fill="#2a4a8a"/></svg></div>
  <div class="svc-icon" style="left:717px"><svg width="22" height="22" viewBox="0 0 22 22"><rect x="3" y="13" width="3" height="6" fill="#fff"/><rect x="8" y="10" width="3" height="9" fill="#fff"/><rect x="13" y="7" width="3" height="12" fill="#fff"/><rect x="18" y="4" width="2" height="15" fill="#fff"/></svg></div>
  <div class="svc-icon" style="left:997px"><svg width="24" height="22" viewBox="0 0 24 22"><path d="M3 14 5 8H19L21 14V17H3Z" fill="#fff"/><circle cx="7" cy="17" r="2" fill="#2a4a8a"/><circle cx="17" cy="17" r="2" fill="#2a4a8a"/></svg></div>

  <div class="svc-label" style="left:62px">Criminal Charges</div>
  <div class="svc-label" style="left:343px">Estate Planning</div>
  <div class="svc-label" style="left:624px">Capital Market</div>
  <div class="svc-label" style="left:904px">Personal Injury</div>
</section>

<section class="mail">
  <h2>Feel Free to Mail</h2>
  <div class="field" style="left:49px;top:76px">Name *</div>
  <div class="field" style="left:310px;top:76px">Phone Number *</div>
  <div class="field" style="left:49px;top:127px">Email *</div>
  <div class="send" style="left:310px;top:127px">SEND MESSAGE</div>
</section>
<section class="inhouse">
  <h2>In-house Legal Services</h2>
  <p>We have a range of services to help in-house lawyers. Take a look and see how we can help you and your team.</p>
  <span class="btn-outline">LEARN MORE</span>
</section>

<h2 class="section-title" style="top:1167px">Latest <span>Blog &amp; Posts</span></h2>
<div class="section-rule" style="top:1205px"></div>

<article class="post" style="left:51px">
  <div class="post-img" style="background:linear-gradient(135deg,#b9b2a8,#7a4a2a)" role="img" aria-label="Photo of a traveller walking with a leather bag"></div>
  <h3>Standard Post</h3>
  <p>Enim congue blandit. Lorem ipsum dolor sit amet, consectetur adipiscing elit. Quisque...</p>
  <div class="post-meta"><span>▦ 22 June, 2015</span><span>● 0</span></div>
</article>
<article class="post" style="left:332px">
  <div class="post-img" style="background:linear-gradient(135deg,#d9d5cf,#6f6459)" role="img" aria-label="Photo of a coffee carafe on a table"></div>
  <h3>Video Post</h3>
  <p>Ultrices posuere cubilia curae curabitur sit amet tortor ut massa commodo. Vestibulum...</p>
  <div class="post-meta"><span>▦ 22 June, 2015</span><span>● 0</span></div>
</article>
<article class="post" style="left:614px">
  <div class="post-img" style="background:linear-gradient(135deg,#8a5a43,#c9b59a)" role="img" aria-label="Photo of a café table against a brick wall"></div>
  <h3>Post with Image</h3>
  <p>Enim congue blandit. Lorem ipsum dolor sit amet, consectetur adipiscing elit. Quisque...</p>
  <div class="post-meta"><span>▦ 22 June, 2015</span><span>● 0</span></div>
</article>
<article class="post" style="left:896px">
  <div class="post-img" style="background:linear-gradient(135deg,#cfc6b8,#7a5a44)" role="img" aria-label="Photo of a leather wallet on a table"></div>
  <h3>Image Post</h3>
  <p>Ultrices posuere cubilia curae curabitur sit amet tortor ut massa commodo. Vestibulum...</p>
  <div class="post-meta"><span>▦ 22 June, 2015</span><span>● 3</span></div>
</article>

<section class="testimonials">
  <h2 class="section-title" style="top:20px">What <span>People Say</span></h2>
  <div class="section-rule" style="top:57px"></div>
  <blockquote class="quote" style="left:51px;text-align:right">Duis aute irure dolor in reprehenderit in voluptate velit esse cillum dolore eu fugiat nulla pariatur. Excepteur sint occaecat cupidatat non proident, sunt in culpa qui officia deserunt mollit.<cite>Marc Renaud, Operations Manager</cite></blockquote>
  <div class="avatar" style="left:491px" role="img" aria-label="Client portrait"></div>
  <div class="divider-v"></div>
  <div class="avatar" style="left:633px" role="img" aria-label="Client portrait"></div>
  <blockquote class="quote" style="left:738px;width:400px">Provident, similique sunt in culpa qui officia deserunt mollitia animi, id est laborum et dolorum fuga. Et harum quidem rerum facilis est et expedita distinctio. Nam libero tempore, cum soluta nobis.<cite>Sara Brunner, Creative Designer</cite></blockquote>
</section>

<section class="likebar">
  <div class="line"></div>
  <div class="like-pill">
    <div class="thumb"><svg width="18" height="16" viewBox="0 0 18 16"><rect x="1" y="7" width="4" height="8" fill="#c9ccd2"/><path d="M6 7 9 1C11 1 11 3 10.5 6H16V10L14 15H6Z" fill="#c9ccd2"/></svg></div>
    <span class="like-btn">✓ Like</span><small>You and 4k others like this.</small>
  </div>
</section>

<footer class="footer">
  <h4 style="left:51px">Contact Us</h4>
  <h4 style="left:0;width:1200px;text-align:center">Headquarters</h4>
  <h4 style="left:896px">About Team</h4>
  <div class="contact-col">
    <p>Please feel free to contact us for any issue. Our staff is available to you from 9AM until 5PM on weekdays.</p>
    <p><b>Phone:</b> +41 44 210 58 90</p>
    <p><b>Office:</b> Company Address Here</p>
    <p><b>Email:</b> hello@kova-legal.ch</p>
    <div class="socials"><i></i><i></i><i></i><i></i><i></i></div>
  </div>
  <div class="map" role="img" aria-label="Street map showing the headquarters location"></div>
  <div class="about-col">
    <p>Enim congue blandit. Lorem ipsum dolor sit amet, consectetur adipiscing elit. Quisque consectetur interdum finibus. Vestibulum ante ipsum primis in faucibus orci. luctus et ultrices posuere.</p>
    <p>Cubilia cras blandit finibus ipsum, id porttitor arcu volutpat a. Integer iaculis erat nec justo malesuada faucibus vel tempus sapien. Vivamus aliquam euismod tristique.</p>
  </div>
  <div class="rule"></div>
  <div class="copy" style="left:51px">Copyright © Kova</div>
  <div class="foot-brand">KOVA</div>
  <div class="copy" style="right:51px">All rights reserved</div>
</footer>

</body>
</html>
```